MV Decor

There is a sample provided with the arabic text of the business card. please copy paste the same text and the same Logo (The two triangles) Just try to incorproate the Brown background attached (you are free to change the colors) Id like the colors to be mainly shades of black and red.

```html
<!DOCTYPE html>
<html lang="ar">
<head>
<meta charset="utf-8">
<title>MV Decor — Business Card</title>
<link href="https://fonts.googleapis.com/css2?family=Cairo:wght@400;600;700&family=Aref+Ruqaa:wght@400;700&display=swap" rel="stylesheet">
<style>
  :root {
    --stage: #5b3a26;
    --card-red: #cf1f45;
    --card-red-light: #e0375b;
    --card-red-dark: #b8163a;
    --ink-white: #ffffff;
    --ink-black: #232322;
    --shadow: rgba(0, 0, 0, 0.45);
  }
  * { box-sizing: border-box; margin: 0; padding: 0; }
  html, body {
    width: 1125px;
    height: 1200px;
    overflow: hidden;
    background: var(--stage);
  }
  .stage { position: relative; width: 1125px; height: 1200px; }
  .card {
    position: absolute;
    left: 171px;
    width: 825px;
    height: 472px;
    background: var(--card-red);
    box-shadow: 0 3px 8px var(--shadow);
    overflow: hidden;
    color: var(--ink-white);
  }
  .card--front { top: 106px; }
  .card--back { top: 639px; }
  .card-texture {
    position: absolute;
    inset: 0;
    background:
      radial-gradient(ellipse at 35% 30%, var(--card-red-light) 0%, transparent 55%),
      radial-gradient(ellipse at 80% 80%, var(--card-red-dark) 0%, transparent 60%),
      var(--card-red);
  }
  .brand-name {
    position: absolute;
    font-family: "Cairo", sans-serif;
    font-weight: 700;
    color: var(--ink-white);
    letter-spacing: 2px;
    display: flex;
    align-items: center;
    gap: 12px;
    white-space: nowrap;
    line-height: 1;
  }
  .brand-mark { display: inline-block; background: var(--ink-black); }
  .card--front .brand-name { left: 56px; top: 204px; font-size: 34px; }
  .card--front .brand-mark { width: 22px; height: 22px; }
  .credentials {
    position: absolute;
    right: 535px;
    top: 262px;
    list-style: none;
    direction: rtl;
    text-align: right;
    font-family: "Cairo", sans-serif;
    font-size: 19px;
    line-height: 28px;
    letter-spacing: 0.5px;
    white-space: nowrap;
  }
  .phone {
    position: absolute;
    left: 57px;
    top: 386px;
    display: flex;
    align-items: center;
    gap: 6px;
    font-family: "Cairo", sans-serif;
    font-weight: 600;
    font-size: 21px;
    direction: ltr;
  }
  .phone svg { width: 19px; height: 19px; }
  .holder {
    position: absolute;
    right: 67px;
    top: 280px;
    direction: rtl;
    text-align: center;
    font-family: "Aref Ruqaa", serif;
    white-space: nowrap;
  }
  .holder-name { font-size: 26px; line-height: 34px; }
  .holder-title { font-size: 18px; line-height: 26px; }
  .card--back .brand-name {
    left: 127px;
    top: 221px;
    width: 245px;
    justify-content: center;
    font-size: 38px;
  }
  .card--back .brand-mark { width: 26px; height: 26px; }
  .services {
    position: absolute;
    right: 114px;
    top: 104px;
    list-style: none;
    direction: rtl;
    text-align: right;
    font-family: "Cairo", sans-serif;
    font-size: 23px;
    line-height: 33.5px;
    letter-spacing: 0.5px;
    white-space: nowrap;
  }
  .services li::after {
    content: "";
    display: inline-block;
    width: 8px;
    height: 8px;
    border-radius: 50%;
    background: var(--ink-white);
    margin-right: 14px;
    vertical-align: middle;
  }
</style>
</head>
<body>
<main class="stage">
  <section class="card card--front">
    <div class="card-texture" role="img" aria-label="Red background with soft grid of small squares and dots"></div>
    <div class="brand-name"><span class="brand-mark"></span>MV DECOR</div>
    <ul class="credentials">
      <li>ماجستير تصميم داخلي</li>
      <li>دبلوم عالي فنون بصرية</li>
      <li>أكاديمية الفنون الحديثة</li>
      <li>استشارات تصميم-ديكور</li>
    </ul>
    <div class="phone">
      <svg viewBox="0 0 24 24" aria-hidden="true"><path fill="#ffffff" d="M6.6 10.8a15.1 15.1 0 0 0 6.6 6.6l2.2-2.2a1 1 0 0 1 1-.25 11.4 11.4 0 0 0 3.6.57 1 1 0 0 1 1 1V20a1 1 0 0 1-1 1A17 17 0 0 1 3 4a1 1 0 0 1 1-1h3.5a1 1 0 0 1 1 1c0 1.25.2 2.45.57 3.57a1 1 0 0 1-.25 1z"/></svg>
      <span>31234567 / 65432100</span>
    </div>
    <div class="holder">
      <p class="holder-name">المهندس / سالم يوسف الراشد</p>
      <p class="holder-title">أستاذ جامعي</p>
    </div>
  </section>

  <section class="card card--back">
    <div class="card-texture" role="img" aria-label="Red background with soft grid of small squares and dots"></div>
    <div class="brand-name"><span class="brand-mark"></span>MV DECOR</div>
    <ul class="services">
      <li>ماجستير تصميم داخلي</li>
      <li>دبلوم عالي فنون بصرية</li>
      <li>أكاديمية الفنون الحديثة</li>
      <li>استشارات تصميم-ديكور</li>
      <li>ماجستير تصميم داخلي</li>
      <li>دبلوم عالي فنون بصرية</li>
      <li>أكاديمية الفنون الحديثة</li>
      <li>استشارات تصميم-ديكور</li>
    </ul>
  </section>
</main>
</body>
</html>
```